Interior Decorating business - Logo & Stationery

"Willowmere Studio" is a newly established interior decorating company, based in Sydney, providing interior decorating, colour consulting and property styling services to residential and commercial clients.

We require a logo and stationery design (double-sided business card, A4 letterhead and with compliments slip (210mm X 95mm))

Letterhead information and with compliments slip:
Address - 9/31-33 Farrowdale St, Penhaven NSW 2047
Phone - (02)9617 4280
Mobile - 0432 581 906
Email - maren@willowmerestudio.com.au
Web - www.willowmerestudio.com.au
ABN - 47832915064

Business Cards should be double sided and are to include;
Maren Holcroft
Director

with email address, mobile number, website as listed above

They also need to include services offered i.e. Interior Decorating, Colour Consulting, Property Styling

Please note that the current content on the website will be updated, so disregard logo and content currently on the website.

Target Market(s)

Target market is two-fold - residential clients (primarily homeowners with pride in their homes) and commerical clients (specifically business owners of retail shops and cafes and property developers)

Industry/Entity Type

Residential

```html
<!DOCTYPE html>
<html lang="en">
<head>
<meta charset="utf-8">
<title>Willowmere Studio – Logo &amp; Stationery</title>
<link rel="stylesheet" href="https://fonts.googleapis.com/css2?family=Arimo:wght@400;700&family=Tinos:ital@0;1&display=swap">
<style>
  :root {
    --green: #6aa625;
    --green-dark: #5b9420;
    --green-text: #5f9b22;
    --lime: #b8d62e;
    --paper: #ffffff;
    --ink: #3c3c3c;
    --shadow: 0 2px 8px rgba(0,0,0,0.28);
  }
  * { box-sizing: border-box; margin: 0; padding: 0; }
  html, body { width: 1200px; height: 900px; overflow: hidden; background: var(--paper); }
  body { position: relative; font-family: "Arimo", Arial, sans-serif; color: var(--green-text); }

  .brand { position: absolute; display: flex; align-items: center; gap: 0.35em; color: var(--green); font-family: "Arimo", Arial, sans-serif; font-weight: 400; white-space: nowrap; letter-spacing: 0.01em; }
  .brand__dot { width: 0.7em; height: 0.7em; border-radius: 50%; background: var(--lime); flex: none; }
  .brand--light { color: var(--paper); }
  .brand--light .brand__dot { background: var(--paper); }

  .sheet { position: absolute; background: var(--paper); box-shadow: var(--shadow); }

  .master-logo { left: 40px; top: 42px; font-size: 62px; }

  .card-back { left: 660px; top: 60px; width: 480px; height: 186px; background: var(--green); }
  .card-back .brand { left: 50%; top: 50%; transform: translate(-50%, -50%); font-size: 44px; }

  .details { position: absolute; font-weight: 700; font-size: 13px; line-height: 1.2; color: var(--green-text); }
  .phones { position: absolute; font-size: 10px; line-height: 1.45; color: var(--green-text); text-align: left; }

  .services { position: absolute; display: flex; align-items: center; font-weight: 700; font-size: 12px; color: var(--green-text); white-space: nowrap; }
  .services__sep { display: inline-block; width: 2px; height: 12px; background: var(--green-text); margin: 0 22px; }

  /* Letterhead */
  .letterhead { left: 30px; top: 324px; width: 560px; height: 546px; }
  .letterhead .details { left: 22px; top: 16px; }
  .letterhead .brand { right: 22px; top: 22px; font-size: 26px; }
  .letterhead__rule { position: absolute; left: 20px; top: 86px; width: 338px; height: 5px; background: var(--green); }
  .letterhead .phones { right: 24px; top: 92px; }
  .letterhead .services { right: 24px; bottom: 40px; font-size: 11px; }

  /* Business card front */
  .card-front { left: 660px; top: 310px; width: 496px; height: 226px; }
  .card-front .brand { left: 14px; top: 22px; font-size: 24px; }
  .person { position: absolute; right: 24px; top: 36px; text-align: center; font-family: "Tinos", "Times New Roman", serif; color: var(--green-text); }
  .person__name { font-size: 36px; line-height: 1; }
  .person__role { font-size: 24px; line-height: 1.2; }
  .card-front .details { left: 14px; top: 100px; font-size: 12.5px; }
  .card-front .phones { right: 16px; top: 130px; }
  .card-front .services { left: 14px; right: 16px; top: 172px; justify-content: space-between; font-size: 12.5px; }
  .card-front .services__sep { margin: 0; }
  .card-strip { position: absolute; left: 0; right: 0; bottom: 0; height: 20px; background: var(--green); color: var(--paper); font-weight: 700; font-size: 11px; letter-spacing: 0.62em; display: flex; align-items: center; justify-content: center; }

  /* Compliments slip */
  .slip { left: 610px; top: 584px; width: 554px; height: 236px; }
  .slip .brand { left: 14px; top: 26px; font-size: 26px; }
  .slip .details { left: 316px; top: 14px; font-size: 12.5px; }
  .slip .phones { left: 316px; top: 62px; }
  .slip__greeting { position: absolute; left: 22px; top: 110px; font-family: "Tinos", "Times New Roman", serif; font-style: italic; font-size: 34px; color: var(--green-text); }
  .slip .services { left: 26px; bottom: 16px; font-size: 11.5px; }
  .slip .services__sep { margin: 0 34px; }
</style>
</head>
<body>

  <div class="brand master-logo"><span class="brand__dot"></span>Willowmere Studio</div>

  <section class="sheet card-back" aria-label="Business card, reverse">
    <div class="brand brand--light"><span class="brand__dot"></span>Willowmere Studio</div>
  </section>

  <section class="sheet letterhead" aria-label="Letterhead">
    <div class="details">
      Address - 9/31-33 Farrowdale St,<br>
      Penhaven NSW 2047<br>
      Email - maren@willowmerestudio.com.au<br>
      Web - www.willowmerestudio.com.au
    </div>
    <div class="brand"><span class="brand__dot"></span>Willowmere Studio</div>
    <div class="letterhead__rule"></div>
    <div class="phones">Phone - (02)9617 4280<br>Mobile - 0432 581 906</div>
    <div class="services">Interior Decorating<span class="services__sep"></span>Colour Consulting<span class="services__sep"></span>Property Styling</div>
  </section>

  <section class="sheet card-front" aria-label="Business card, front">
    <div class="brand"><span class="brand__dot"></span>Willowmere Studio</div>
    <div class="person">
      <div class="person__name">Maren Holcroft</div>
      <div class="person__role">Director</div>
    </div>
    <div class="details">
      Address - 9/31-33 Farrowdale St,<br>
      Penhaven NSW 2047<br>
      Email - maren@willowmerestudio.com.au<br>
      Web - www.willowmerestudio.com.au
    </div>
    <div class="phones">Phone - (02)9617 4280<br>Mobile - 0432 581 906</div>
    <div class="services">Interior Decorating<span class="services__sep"></span>Colour Consulting<span class="services__sep"></span>Property Styling</div>
    <div class="card-strip">www.willowmerestudio.com</div>
  </section>

  <section class="sheet slip" aria-label="With compliments slip">
    <div class="brand"><span class="brand__dot"></span>Willowmere Studio</div>
    <div class="details">
      Address - 9/31-33 Farrowdale St,<br>
      Penhaven NSW 2047<br>
      Web - www.willowmerestudio.com.au
    </div>
    <div class="phones">Phone - (02)9617 4280<br>Mobile - 0432 581 906</div>
    <p class="slip__greeting">With compliments....</p>
    <div class="services">Interior Decorating<span class="services__sep"></span>Colour Consulting<span class="services__sep"></span>Property Styling</div>
  </section>

</body>
</html>
```